New Fun, Positive, energised looking Business Card Needed for High Achiever Coach

I am looking for a two sided full colour business card. I am self employed and have recently re branded my 1-2-1 work re-vitalising high achievers. My target client base for these cards is therefore high achievers - usually aged 40 -55, they are often entrepreneurs, CEO or work in banking and finance and 2/3 are male. I work with them on 90 day or 6 month coaching programs to help them live their success in a healthier, more sustainable and fulfiiled way. They pay for this privately so though they are corporate types the cards need not look 'corporate'. I want to portray the idea of transformation, vitality and re-connecting.
You can get a feel for the look I like on my new website: morvenlisk.co.uk
I want to use this logo with strapline (Re-Vitalising High Achievers) (I purchased off Logoharbor) and font/ colours (the turquoise and green).
Details to include on the card:
www.morvenlisk.co.uk
+44 7915 302618
morven@morvenlisk.co.uk
skype: morvenlisk
I'd also like to include:
Do you struggle to switch off? Want to be healthier and feel fitter? Want closer relationships? More clarity over the direction you are headed? I can help you do these things using integrated mind-body techniques. Visit morvenlisk.co.uk TODAY to apply for a FREE Breakthrough session.
BUT if that is too much text for a card I am open to advice/ammendments.
Updates
Thanks for your design - I am considering them. PLease change the wording to :

```html
<!DOCTYPE html>
<html lang="en">
<head>
<meta charset="utf-8">
<title>Morven Lisk – Business Card</title>
<link rel="stylesheet" href="https://fonts.googleapis.com/css2?family=Open+Sans:ital,wght@0,400;0,700;1,400&family=Great+Vibes&display=swap">
<style>
  :root {
    --turquoise: #1a9fc0;
    --green: #5bb85d;
    --card-white: #ffffff;
    --card-black: #0b0b0b;
    --ink-light: #f2f2f2;
    --backdrop: #e7e4df;
  }
  * { box-sizing: border-box; margin: 0; padding: 0; }
  html, body { width: 1200px; height: 900px; overflow: hidden; }
  body {
    background: var(--backdrop);
    font-family: "Open Sans", Arial, sans-serif;
    position: relative;
  }
  .card {
    position: absolute;
    left: 300px;
    width: 600px;
    height: 345px;
    border-radius: 22px;
    overflow: hidden;
    box-shadow: 0 6px 18px rgba(0,0,0,0.18);
  }
  .card--front { top: 80px; background: var(--card-white); }
  .card--back  { top: 475px; background: var(--card-black); }

  /* front */
  .brand {
    position: absolute;
    left: 60px; top: 52px;
    display: flex; align-items: center; gap: 10px;
  }
  .brand__dot {
    width: 18px; height: 18px; border-radius: 50%;
    background: var(--green);
  }
  .brand__name {
    font-weight: 700;
    font-size: 24px;
    color: var(--turquoise);
    letter-spacing: 0.3px;
  }
  .holder-name {
    position: absolute;
    left: 70px; top: 108px;
    font-family: "Great Vibes", cursive;
    font-size: 52px;
    color: var(--turquoise);
  }
  .rule {
    position: absolute;
    left: 40px; right: 40px; top: 218px;
    height: 2px; background: var(--turquoise);
  }
  .contacts {
    position: absolute;
    left: 48px; right: 40px; top: 240px;
    display: flex; align-items: center;
  }
  .contacts__col { display: flex; flex-direction: column; gap: 12px; }
  .contacts__divider {
    width: 2px; height: 46px; background: var(--turquoise);
    margin: 0 40px;
  }
  .contact {
    display: flex; align-items: center; gap: 9px;
    font-size: 15px; color: var(--turquoise);
  }
  .contact svg { width: 17px; height: 17px; flex: none; }

  /* back */
  .back__accent {
    position: absolute; left: 0; top: 34px;
    width: 8px; height: 26px; background: var(--turquoise);
  }
  .pitch {
    position: absolute;
    left: 34px; top: 32px; width: 380px;
    font-style: italic;
    font-size: 12.5px; line-height: 1.55;
    color: var(--ink-light);
  }
  .pitch__link { color: var(--turquoise); }
  .brand--back { left: auto; right: 48px; top: auto; bottom: 46px; }
  .brand--back .brand__name { font-size: 30px; }
  .brand--back .brand__dot { width: 22px; height: 22px; }
</style>
</head>
<body>

<section class="card card--front" aria-label="Card front">
  <div class="brand">
    <span class="brand__dot"></span>
    <span class="brand__name">Morven Lisk</span>
  </div>
  <div class="holder-name">Your Name</div>
  <div class="rule"></div>
  <div class="contacts">
    <div class="contacts__col">
      <div class="contact">
        <svg viewBox="0 0 24 24" fill="currentColor" aria-hidden="true"><path d="M6.6 10.8a15.1 15.1 0 0 0 6.6 6.6l2.2-2.2a1 1 0 0 1 1-.25 11.4 11.4 0 0 0 3.6.57 1 1 0 0 1 1 1V20a1 1 0 0 1-1 1A17 17 0 0 1 3 4a1 1 0 0 1 1-1h3.5a1 1 0 0 1 1 1c0 1.25.2 2.45.57 3.57a1 1 0 0 1-.25 1z"/></svg>
        <span>+44 7915 302618</span>
      </div>
      <div class="contact">
        <svg viewBox="0 0 24 24" fill="currentColor" aria-hidden="true"><path d="M3 5h18a1 1 0 0 1 1 1v12a1 1 0 0 1-1 1H3a1 1 0 0 1-1-1V6a1 1 0 0 1 1-1zm9 7.5L20 7H4z"/></svg>
        <span>morven@morvenlisk.co.uk</span>
      </div>
    </div>
    <div class="contacts__divider"></div>
    <div class="contacts__col">
      <div class="contact">
        <svg viewBox="0 0 24 24" aria-hidden="true"><circle cx="12" cy="12" r="10" fill="currentColor"/></svg>
        <span>morvenlisk</span>
      </div>
      <div class="contact">
        <svg viewBox="0 0 24 24" fill="none" stroke="currentColor" stroke-width="2" aria-hidden="true"><circle cx="12" cy="12" r="9.5"/><path d="M2.5 12h19M12 2.5c3 3 3 16 0 19M12 2.5c-3 3-3 16 0 19"/></svg>
        <span>www.morvenlisk.co.uk</span>
      </div>
    </div>
  </div>
</section>

<section class="card card--back" aria-label="Card back">
  <div class="back__accent"></div>
  <p class="pitch">
    Do you struggle to switch off?<br>
    Want to be healthier and feel fitter?<br>
    Want closer relationships?<br>
    More clarity over the direction you are headed?<br>
    I can help you do these things using integrated mind-body techniques.<br>
    Visit <span class="pitch__link">morvenlisk.co.uk</span> TODAY to apply for a FREE Breakthrough session.
  </p>
  <div class="brand brand--back">
    <span class="brand__dot"></span>
    <span class="brand__name">Morven Lisk</span>
  </div>
</section>

</body>
</html>
```